Garlic Farm for Farm Sales/Restaurant sales

Need a professional, but appealing to agriculture world. We are selling 27 kinds of Organic Garlic from a farm in Simla,CO. I have uploaded logo and business information-we are going to need a template, because I will need to use it for four separate people.
-We are trying to appeal to Farm to table restaurants
-As well as growers/farmers

Target Market(s)

Agriculture Sales/Restaurants-Organic

Industry/Entity Type

Agriculture

Contact Information for Business Card

Want it to look more unique then your average kelto stock card- I want it to look amazing

Font styles to use
Sans Serif

Colors
0455a3
ec1f27
fbed22
ffffff

Requirements
Must have
• Just be creative
Nice to have
• Colorful
Should not have
• plain

```html
<!DOCTYPE html>
<html lang="en">
<head>
<meta charset="utf-8">
<title>Plains Ridge Garlic – Business Card</title>
<link rel="stylesheet" href="https://fonts.googleapis.com/css2?family=Varela+Round&family=Nunito:wght@700&display=swap">
<style>
  :root {
    --navy: #1f3679;
    --red: #d8263f;
    --red-deep: #c41d33;
    --red-light: #dc3048;
    --yellow: #fbed22;
    --white: #ffffff;
    --paper: #fbfbfb;
    --ink: #2a2a2a;
    --stage: #e9e5df;
  }
  * { box-sizing: border-box; margin: 0; padding: 0; }
  html, body {
    width: 1200px;
    height: 892px;
    overflow: hidden;
    background: var(--stage);
  }
  .canvas {
    width: 1200px;
    height: 892px;
    display: flex;
    align-items: center;
    justify-content: center;
    gap: 80px;
  }
  .card {
    width: 400px;
    height: 660px;
    border-radius: 6px;
    box-shadow: 0 10px 28px rgba(0, 0, 0, 0.18);
    position: relative;
    overflow: hidden;
    font-family: "Varela Round", sans-serif;
  }

  /* Front */
  .card-front { background: var(--paper); }
  .brand {
    position: absolute;
    top: 96px;
    left: 0;
    right: 0;
    display: flex;
    align-items: center;
    justify-content: center;
    gap: 18px;
  }
  .brand-dot {
    width: 64px;
    height: 64px;
    border-radius: 50%;
    background: var(--red);
    flex: none;
  }
  .brand-name {
    font-size: 36px;
    color: var(--navy);
    letter-spacing: 1px;
    line-height: 1.1;
  }
  .person {
    position: absolute;
    top: 300px;
    left: 42px;
    right: 24px;
  }
  .person-name {
    font-size: 46px;
    color: var(--ink);
    letter-spacing: 1px;
    white-space: nowrap;
  }
  .person-phone {
    margin-top: 40px;
    font-size: 36px;
    color: var(--ink);
    letter-spacing: 1px;
    white-space: nowrap;
  }
  .front-band {
    position: absolute;
    left: 0;
    right: 0;
    bottom: 0;
    height: 110px;
    background: var(--red);
  }

  /* Back */
  .card-back {
    background: radial-gradient(circle at 45% 35%, var(--red-light) 0%, var(--red) 45%, var(--red-deep) 100%);
    color: var(--white);
  }
  .back-brand {
    position: absolute;
    top: 130px;
    left: 0;
    right: 0;
    display: flex;
    align-items: center;
    justify-content: center;
    gap: 18px;
  }
  .back-brand .brand-dot {
    background: var(--yellow);
    width: 72px;
    height: 72px;
  }
  .back-brand .brand-name {
    font-size: 46px;
    white-space: nowrap;
  }
  .specialty {
    position: absolute;
    top: 330px;
    left: 40px;
    right: 24px;
  }
  .specialty-title {
    font-family: "Nunito", sans-serif;
    font-weight: 700;
    font-size: 32px;
  }
  .specialty-list {
    margin-top: 16px;
    font-size: 21px;
    line-height: 1.6;
    white-space: nowrap;
  }
</style>
</head>
<body>
  <main class="canvas">
    <section class="card card-front" aria-label="Business card front">
      <div class="brand">
        <span class="brand-dot"></span>
        <span class="brand-name">Plains Ridge<br>Garlic</span>
      </div>
      <div class="person">
        <p class="person-name">Dana Hollis</p>
        <p class="person-phone">555 014-2297</p>
      </div>
      <div class="front-band"></div>
    </section>

    <section class="card card-back" aria-label="Business card back">
      <div class="back-brand">
        <span class="brand-dot"></span>
        <span class="brand-name">plains ridge</span>
      </div>
      <div class="specialty">
        <p class="specialty-title">Specializing in:</p>
        <p class="specialty-list">personalized gifts for babies<br>weddings and pets</p>
      </div>
    </section>
  </main>
</body>
</html>
```